FunBrixo Business Card

We need a business card design for our company. We sell construction-themed amusement rides for kids.

Contact Information for Business Card

Contact info on business card should include:
Carl Dunning
Co-Founder & COO
(833) 571-FUNBRIX
Carl@funbrixo-demo.com
www.funbrixo-demo.com

```html
<!DOCTYPE html>
<html lang="en">
<head>
<meta charset="utf-8">
<title>FunBrixo Business Card</title>
<link rel="stylesheet" href="https://fonts.googleapis.com/css2?family=Roboto:wght@400;500;700;900&display=swap">
<style>
  :root {
    --stage: #e9e9e9;
    --card: #050505;
    --edge: #f07a22;
    --orange: #f0802a;
    --white: #f2f2f2;
    --muted: #bdbdbd;
    --rule: #8a8a8a;
    --ghost: #1c1c1c;
  }
  * { box-sizing: border-box; margin: 0; padding: 0; }
  html, body {
    width: 1200px; height: 801px; overflow: hidden;
    background: var(--stage);
    font-family: "Roboto", Arial, sans-serif;
  }
  .sheet {
    position: relative; width: 1200px; height: 801px;
    display: flex; align-items: center; justify-content: center; gap: 40px;
  }
  .card {
    position: relative; width: 540px; height: 310px;
    background: var(--card);
    border-bottom: 3px solid var(--edge);
    border-left: 2px solid var(--edge);
    box-shadow: 0 10px 24px rgba(0,0,0,.25);
    overflow: hidden;
  }
  .ghost-name {
    position: absolute; left: 30px; bottom: 60px;
    font-size: 120px; font-weight: 900; color: var(--ghost);
    letter-spacing: -2px; line-height: 1;
  }
  .front .brand {
    position: absolute; top: 34px; right: 34px;
    display: flex; align-items: center; gap: 10px;
  }
  .brand-dot {
    width: 22px; height: 22px; border-radius: 50%; background: var(--orange);
  }
  .brand-name {
    font-weight: 900; color: var(--orange); line-height: 1;
  }
  .front .brand-name { font-size: 40px; }
  .divider {
    position: absolute; left: 30px; right: 30px; top: 168px;
    height: 1px; background: var(--rule);
  }
  .person { position: absolute; left: 30px; top: 118px; }
  .person-name { color: var(--orange); font-size: 24px; font-weight: 500; }
  .person-role { color: var(--white); font-size: 15px; margin-top: 2px; }
  .person { top: 112px; }
  .contact {
    position: absolute; left: 30px; top: 186px;
    list-style: none; display: flex; flex-direction: column; gap: 10px;
  }
  .contact li {
    display: flex; align-items: center; gap: 12px;
    color: var(--white); font-size: 16px;
  }
  .contact svg { width: 16px; height: 16px; flex: none; }
  .contact .accent { color: var(--orange); }
  .back { display: flex; align-items: center; justify-content: center; }
  .back .brand { display: flex; align-items: center; gap: 14px; }
  .back .brand-dot { width: 34px; height: 34px; }
  .back .brand-name { font-size: 72px; }
</style>
</head>
<body>
<main class="sheet">
  <section class="card front" aria-label="Card front with contact details">
    <div class="ghost-name" aria-hidden="true">FunBrixo</div>
    <div class="brand">
      <span class="brand-dot"></span>
      <span class="brand-name">FunBrixo</span>
    </div>
    <div class="person">
      <p class="person-name">Carl Dunning</p>
      <p class="person-role">Co-Founder &amp; COO</p>
    </div>
    <div class="divider"></div>
    <ul class="contact">
      <li>
        <svg viewBox="0 0 16 16" aria-hidden="true"><path fill="#f0802a" d="M4 1.5l2.2 3-1.4 1.6c.8 1.8 2.3 3.3 4.1 4.1l1.6-1.4 3 2.2-1.3 2.5C7 13.2 2.8 9 2.5 3z"/></svg>
        <span>(833) 571-FUNBRIX</span>
      </li>
      <li>
        <svg viewBox="0 0 16 16" aria-hidden="true"><rect x="1.5" y="3.5" width="13" height="9" fill="none" stroke="#f0802a" stroke-width="1.5"/><path d="M1.5 3.5l6.5 5 6.5-5" fill="none" stroke="#f0802a" stroke-width="1.5"/></svg>
        <span>Carl@funbrixo-demo.com</span>
      </li>
      <li>
        <svg viewBox="0 0 16 16" aria-hidden="true"><circle cx="8" cy="8" r="6.5" fill="#f0802a"/><path d="M1.5 8h13M8 1.5c-3 3.5-3 9.5 0 13M8 1.5c3 3.5 3 9.5 0 13" fill="none" stroke="#050505" stroke-width="1"/></svg>
        <span>www.<span class="accent">funbrixo-demo</span>.com</span>
      </li>
    </ul>
  </section>

  <section class="card back" aria-label="Card back with brand name">
    <div class="brand">
      <span class="brand-dot"></span>
      <span class="brand-name">FunBrixo</span>
    </div>
  </section>
</main>
</body>
</html>
```